Harborview Estates Business Card for Apartment Buildings

Create business cards for resident managers who run apartment buildings. The audience is the public who are searching for apartment rentals, and current residents who live at the apartment building. Key design element will be incorporating the company logo, however, the logo cannot dominate. The building name and manager name are more important than the logo. Current business card design leaves little room for copy, so we may need to reduce the size on the current card to allow for more space for copy.

Target Market(s)

Adults 18-65 years of age, who are looking for an apartment rental, plus current residents who live at our apartment buildings.

Industry/Entity Type

Property Management

Contact Information for Business Card

A major design element will be use of the company logo. Important property and manager contact information must be part of the design. The size of the logo will need to be reduced to make room for building and manager contact copy.

Font styles to use
Sans Serif

Colors
3176b5
000000
959595
ffffff

Requirements
Must have
• 1) Incorporate the company logo.
• 2) Use the company colors (dark blue, black/grey, over white).
• 3) FEATURE THE BUILDING NAME
• 4) FEATURE THE MANAGER NAME
• 5) The company name is less important than BUILDING and MANAGER
• 6) Manager contact information
• **SEE ATTACHED CREATIVE BRIEF**
Nice to have
• 1) Back of card logo watermark
• 2) Ability to write notes on back of carfd
Should not have
• Avoid letting the company logo dominate the card, the building name and manager are more important than the company logo.

```html
<!DOCTYPE html>
<html lang="en">
<head>
<meta charset="utf-8">
<title>Harborview Estates – Business Card</title>
<link href="https://fonts.googleapis.com/css2?family=Lato:wght@400;700&display=swap" rel="stylesheet">
<style>
  :root {
    --backdrop: #ababab;
    --card-front: #ececec;
    --card-back: #d6d6d6;
    --brand-blue: #1565a8;
    --ink: #2b2b2b;
    --rule: #a6a6a6;
    --disc: #333333;
    --white: #ffffff;
  }
  * { margin: 0; padding: 0; box-sizing: border-box; }
  html, body {
    width: 1200px; height: 900px; overflow: hidden;
    background: var(--backdrop);
    font-family: "Lato", sans-serif;
  }
  .stage { position: relative; width: 1200px; height: 900px; }
  .card {
    position: absolute; top: 170px; width: 347px; height: 560px; overflow: hidden;
  }
  .card--front { left: 259px; background: var(--card-front); text-align: center; color: var(--ink); }
  .card--back { left: 631px; background: var(--card-back); }

  .company-name {
    position: absolute; top: 128px; left: 0; width: 100%;
    color: var(--brand-blue); font-weight: 700; font-size: 27px; line-height: 1.15; letter-spacing: 0.5px;
  }
  .manager { position: absolute; top: 303px; left: 0; width: 100%; }
  .manager__name { color: var(--brand-blue); font-weight: 700; font-size: 25px; letter-spacing: 0.3px; }
  .manager__title { font-size: 15px; margin-top: 1px; }
  .rule { position: absolute; left: 74px; width: 198px; height: 1px; background: var(--rule); }
  .rule--top { top: 361px; }
  .rule--bottom { top: 463px; }
  .contact { position: absolute; top: 371px; left: 0; width: 100%; font-size: 14.5px; line-height: 20px; }
  .contact__label { color: var(--brand-blue); font-weight: 700; }
  .contact__web { color: var(--brand-blue); }
  .address { position: absolute; top: 476px; left: 0; width: 100%; font-size: 14.5px; line-height: 20px; }

  .back-disc {
    position: absolute; left: 24px; top: 188px; width: 350px; height: 350px;
    border-radius: 50%; background: var(--disc);
  }
  .back-name {
    position: absolute; left: 54px; top: 330px; width: 290px;
    color: var(--white); font-weight: 700; font-size: 26px; line-height: 1.2; letter-spacing: 0.5px;
  }
</style>
</head>
<body>
<div class="stage">
  <section class="card card--front">
    <div class="company-name">HARBORVIEW<br>ESTATES LLC</div>
    <div class="manager">
      <div class="manager__name">DANIEL BROOKS</div>
      <div class="manager__title">Property Manager</div>
    </div>
    <div class="rule rule--top"></div>
    <div class="contact">
      <div><span class="contact__label">P:</span> 503-555-0147</div>
      <div><span class="contact__label">F:</span> 503-555-0192</div>
      <div><span class="contact__label">E:</span> daniel@harborviewestates.us</div>
      <div class="contact__web">www.harborviewestates.us</div>
    </div>
    <div class="rule rule--bottom"></div>
    <div class="address">
      <div>1287 Bayline Avenue #B210</div>
      <div>Portland, OR 97204</div>
    </div>
  </section>

  <section class="card card--back">
    <div class="back-disc"></div>
    <div class="back-name">HARBORVIEW<br>ESTATES</div>
  </section>
</div>
</body>
</html>
```